Creative UI design for web application

I need a new UI design for my web application. It will be used by small and micro business owners to plan & implement growth tactics.

I've attached the current design (which I'm open to be changed) - but in particular I need to design the centre of the screen, where the work actually happens.

There needs to be place for a title (YOUR BUSINESS) and description (say 1-2 paragraphs of text) - and am happy to include icons or imagery where makes sense. It may make sense for the user to be able to upload their business logo and name, for example.

This screen will be used by the business owner to understand the real value they offer potential customers and their point of difference - why they exist and why potential customers should care.

They'll use the information they put into this screen to plan things like their messaging.

Following that, there needs to be 2 sections in the dashboard.

The first section is titled "WHO YOU ARE"

The first section will include a number of boxes that the user can input information into, as follows:

- Logo
- Business name
- Business tag line
- Business vision
- Business bio
- Brand colours (these should end up as swatches based on the colour code they enter) - the colour code for each colour swatch should also be visible.
- Key competitors
- SWOT analysis (boxes to enter their strengths, weaknesses, opportunities and threats).

The second section is titled "WHY YOU EXIST"

The second section will include a number of boxes that the user can input information (text) into, as follows:

- Who are your ideal customers?
- What problem are you trying to solve for them?
- What pain points will this remove for them?
- How do you solve it?
- How else could this problem be solved?
- Who offers these other solutions?
- Why is your solution better?
- How much does your solution cost?
- What value are you providing to justify this cost?
- How will this make their life/job easier/better?

They should be able to write a decent amount of information in the boxes.

There should ideally be a place for a description for each of these text fields (for both section 1 & 2) as well so I can give them a little bit more direction around what to put in the box. Alternatively there could be a little icon (say a question mark or "i") that they could click on to view instructions. The instructions will be around 2-4 sentences long for each text field.

You have 2 options:

a) This all needs to appear on the one screen, and the navigation needs to be visible (as per the example attached but feel free to recreate this navigation)

Note: the page can scroll below the fold - but please provide the design for the full length of the page.

b) Potentially the 2 sections could actually be in 2 different items in the menu - YOUR BUSINESS and YOUR VALUE (which would sit next to YOUR BUSINESS and before YOUR CUSTOMER in the screenshot provided). feel free to design them as 2 separate screens if you prefer.

I have attached a screenshot of the app as it stands today (screen shot 2017) which would still exist in the new design but under a different section (the learn section from the plan2 mockup attached)

I have mocked up how this new screen could look if broken into 2 and that's also attached. If you can make this come to life - and look more engaging that would be helpful! :)

Target Market(s)

Small and micro business owners

Industry/Entity Type

Marketing

Number of Pages Required

1 page

Font styles to use
Sans Serif
Other font styles liked:
• Montserrat

Colors
87cfc6
d2a4cc
ffffff
85cae6
e8e8e8
5c5c5c

Requirements
Must have
• Use of my brand colours: #cc8eb2, #76d6c8, #68c7ff as well as white and #595959. Must be visually pleasing / engaging, designed for desktop (as it's a desktop application), really easy to use / navigate.
• Use font Montserrat light & Montserrat Regular or Bold. Mostly should be Montserrat light.
Nice to have
• Would be nice to see how this would look on mobile (as the application is responsive) but this is not mandatory.
Should not have
• Should not look too corporate or dry.

```html
<!DOCTYPE html>
<html lang="en">
<head>
<meta charset="utf-8">
<title>BloomPath – Your Business</title>
<link rel="stylesheet" href="https://fonts.googleapis.com/css2?family=Montserrat:wght@300;400;500;600;700&display=swap">
<style>
:root{
  --pink:#d2a4cc;
  --teal:#87cfc6;
  --teal-deep:#7cc2b9;
  --dark:#2a2a2a;
  --ink:#5c5c5c;
  --heading:#333333;
  --line:#e8e8e8;
  --accent:#d9267f;
  --white:#ffffff;
}
*{box-sizing:border-box;margin:0;padding:0}
html,body{width:1200px;height:2571px;overflow:hidden}
body{font-family:"Montserrat",sans-serif;font-weight:300;color:var(--ink);background:var(--white);position:relative}

/* top navigation */
.topbar{position:absolute;left:0;top:0;width:1200px;height:69px;background:var(--dark)}
.brand{position:absolute;left:99px;top:21px;font-size:24px;font-weight:600;color:var(--white)}
.main-nav{position:absolute;left:442px;top:0;display:flex;height:69px}
.main-nav a{display:flex;align-items:center;padding:0 24px;font-size:16px;font-weight:500;color:var(--white);text-decoration:none;height:69px}
.main-nav a.active{background:var(--pink);font-weight:400}
.user-nav{position:absolute;right:96px;top:26px;display:flex;gap:22px;font-size:12px;font-weight:600;color:var(--white)}
.user-nav span{display:flex;align-items:center;gap:6px}
.subnav{position:absolute;left:0;top:69px;width:1200px;height:54px;background:var(--pink);display:flex;justify-content:flex-end;padding-right:50px}
.subnav a{display:flex;align-items:center;padding:0 21px;font-size:13px;font-weight:500;color:var(--white);text-decoration:none;position:relative}
.subnav a.active::after{content:"";position:absolute;left:0;right:0;bottom:-4px;height:4px;background:var(--teal)}

/* business intro */
.biz-logo{position:absolute;left:99px;top:199px;width:165px;height:165px;border-radius:50%;background:#111;display:flex;align-items:center;justify-content:center;color:var(--white);font-size:22px;font-weight:400}
.biz-name{position:absolute;left:295px;top:222px;font-size:22px;font-weight:400;color:var(--heading);letter-spacing:1px}
.biz-contact{position:absolute;left:295px;top:268px;font-size:13px;display:flex;flex-direction:column;gap:24px}
.biz-contact div{display:flex;align-items:center;gap:10px}
.biz-desc{position:absolute;left:99px;top:382px;width:610px;font-size:12.5px;line-height:25px}
.biz-photo{position:absolute;left:739px;top:197px;width:360px;height:254px;border:3px solid var(--white);box-shadow:0 0 0 1px var(--line);background:linear-gradient(135deg,#caa892,#8a5a4a 55%,#e9d8cf)}

/* who you are */
.who{position:absolute;left:0;top:549px;width:1200px;height:608px;background:linear-gradient(160deg,var(--teal) 0%,#9ad6ce 45%,var(--teal-deep) 100%)}
.section-title{font-size:27px;font-weight:600;text-align:center;letter-spacing:1px}
.who .section-title{color:var(--white);position:absolute;top:58px;width:100%}
.field{position:absolute}
.field label{display:block;font-size:12px;font-weight:500;color:var(--white);margin-bottom:8px}
.field .box{height:34px;border:1px solid rgba(255,255,255,.9);font-size:12.5px;color:var(--white);display:flex;align-items:center;justify-content:space-between;padding:0 14px}
.swatches{display:flex;height:34px;border:1px solid rgba(255,255,255,.9)}
.swatches i{flex:1}
.swatches .gap{flex:6;background:transparent}
.swatches .pick{flex:0 0 22px;background:var(--accent)}
.swot{display:flex;gap:20px}
.swot .box{width:188px}
.notch{position:absolute;left:550px;top:1148px;width:100px;height:42px}

/* why you exist */
.why .section-title{position:absolute;top:1259px;width:100%;color:var(--heading)}
.why-lead{position:absolute;top:1314px;width:100%;text-align:center;font-size:12.5px}
.card{position:absolute;width:484px;height:163px;border:1px solid var(--line);border-radius:8px;overflow:hidden;background:var(--white)}
.card h3{height:38px;background:var(--pink);color:var(--white);font-size:13px;font-weight:500;display:flex;align-items:center;justify-content:space-between;padding:0 20px}
.card p{padding:16px 20px;font-size:12.5px;line-height:23px}
.save{position:absolute;left:490px;top:2372px;width:220px;height:42px;border-radius:8px;background:var(--teal);color:var(--white);font-size:21px;font-weight:600;display:flex;align-items:center;justify-content:center;letter-spacing:1px}

/* footer */
.footer{position:absolute;left:0;top:2482px;width:1200px;height:89px;background:var(--dark);color:var(--white)}
.footer small{position:absolute;left:99px;top:37px;font-size:12px;font-weight:400}
.social{position:absolute;left:930px;top:26px;display:flex;gap:11px}
.social i{width:34px;height:34px;border:2px solid var(--white);border-radius:50%}
</style>
</head>
<body>

<header class="topbar">
  <div class="brand">BloomPath</div>
  <nav class="main-nav">
    <a class="active" href="#">PLAN</a><a href="#">LEARN</a><a href="#">REMEMBER</a>
  </nav>
  <div class="user-nav">
    <span><svg width="11" height="11" viewBox="0 0 10 10"><circle cx="5" cy="3" r="2.5" fill="#fff"/><path d="M0 10a5 4 0 0 1 10 0z" fill="#fff"/></svg>MY PROFILE</span>
    <span><svg width="10" height="11" viewBox="0 0 10 11"><rect x="0" y="5" width="10" height="6" fill="#fff"/><path d="M2.5 5V3a2.5 2.5 0 0 1 5 0v2" stroke="#fff" fill="none" stroke-width="1.5"/></svg>LOG OUT</span>
  </div>
</header>
<nav class="subnav">
  <a class="active" href="#">YOUR BUSINESS</a><a href="#">YOUR PRODUCTS</a><a href="#">YOUR CUSTOMERS</a><a href="#">YOUR GOALS</a><a href="#">YOUR PLAN</a>
</nav>

<section class="intro">
  <div class="biz-logo">Nova</div>
  <h1 class="biz-name">NOVA MAKEUP &amp; HAIR STUDIO</h1>
  <div class="biz-contact">
    <div><svg width="11" height="11" viewBox="0 0 12 12"><path d="M2 0l3 3-1.5 2a7 7 0 0 0 3.5 3.5L9 7l3 3-2 2C5 12 0 7 0 2z" fill="#d9267f"/></svg>(+1) 555 010 2244</div>
    <div><svg width="12" height="9" viewBox="0 0 12 9"><rect width="12" height="9" fill="#d9267f"/><path d="M0 0l6 5 6-5" stroke="#fff" fill="none"/></svg>hello@novastudio.example</div>
  </div>
  <p class="biz-desc">Lorem Ipsum is simply dummy text of the printing and typesetting industry. Lorem Ipsum has been the industry's standard dummy text ever since the 1500s, when an unknown printer took a galley of type and scrambled it to make a type specimen book. It has survived centuries</p>
  <div class="biz-photo" role="img" aria-label="Photo of a makeup artist applying makeup to a client"></div>
</section>

<section class="who">
  <h2 class="section-title">WHO YOU ARE</h2>
  <div class="field" style="left:197px;top:126px;width:382px"><label>LOGO</label><div class="box">Logo image.jpg<svg width="12" height="10" viewBox="0 0 12 10"><rect width="12" height="10" fill="#fff"/><rect x="2" y="2" width="8" height="6" fill="#87cfc6"/></svg></div></div>
  <div class="field" style="left:620px;top:126px;width:383px"><label>BUSINESS NAME</label><div class="box"></div></div>
  <div class="field" style="left:197px;top:210px;width:382px"><label>BUSINESS TAG LINE</label><div class="box"></div></div>
  <div class="field" style="left:620px;top:210px;width:383px"><label>BUSINESS VISION</label><div class="box"></div></div>
  <div class="field" style="left:197px;top:294px;width:382px"><label>BUSINESS BIO</label><div class="box"></div></div>
  <div class="field" style="left:620px;top:294px;width:383px"><label>BRAND COLOURS</label>
    <div class="swatches">
      <i style="background:#e8e3d8"></i><i style="background:#d8d0b8"></i><i style="background:#f3d33a"></i><i style="background:#f5a623"></i><i style="background:#f07b2a"></i><i style="background:#e8432c"></i><i style="background:#d81d4a"></i><i style="background:#c2398f"></i><i style="background:#8e4aa8"></i><i style="background:#5b56b5"></i><i style="background:#2c5fb8"></i><i style="background:#1f8fd0"></i><i style="background:#1aa38a"></i><i style="background:#23a65a"></i><i style="background:#6cbf4a"></i><i style="background:#a8cf55"></i><i style="background:#d4dc7a"></i><i style="background:#f2efd6"></i><i class="gap"></i><i class="pick"></i>
    </div>
  </div>
  <div class="field" style="left:197px;top:381px;width:806px"><label>KEY COMPETITORS</label><div class="box" style="height:48px"></div></div>
  <div class="field" style="left:197px;top:482px;width:806px"><label>SWOT ANALYSIS</label>
    <div class="swot"><div class="box">Strengths</div><div class="box">Weaknesses</div><div class="box">Opportunities</div><div class="box">Threats</div></div>
  </div>
</section>
<svg class="notch" viewBox="0 0 100 42" aria-hidden="true">
  <path d="M0 9 C25 9 28 38 50 38 C72 38 75 9 100 9 L100 0 L0 0Z" fill="#86cbc3"/>
  <path d="M42 15l8 7 8-7M42 22l8 7 8-7" stroke="#fff" stroke-width="2.5" fill="none"/>
</svg>

<section class="why">
  <h2 class="section-title">WHY YOU EXIST</h2>
  <p class="why-lead">The second section will include a number of boxes that the user can input information (text)</p>

  <div class="card" style="left:99px;top:1364px"><h3>WHO ARE YOUR IDEAL CUSTOMERS?<svg width="11" height="11" viewBox="0 0 12 12"><circle cx="6" cy="6" r="6" fill="#fff"/><rect x="5.2" y="5" width="1.6" height="4.5" fill="#d2a4cc"/><circle cx="6" cy="3.3" r=".9" fill="#d2a4cc"/></svg></h3><p>Lorem Ipsum has been the industry's standard dummy text ever since the 1500s, when an unknown printer took a galley of type and scrambled it to make a type specimen book. It has survived</p></div>
  <div class="card" style="left:617px;top:1364px"><h3>WHAT PROBLEM ARE YOU TRYING TO SOLVE FOR THEM?<svg width="11" height="11" viewBox="0 0 12 12"><circle cx="6" cy="6" r="6" fill="#fff"/><rect x="5.2" y="5" width="1.6" height="4.5" fill="#d2a4cc"/><circle cx="6" cy="3.3" r=".9" fill="#d2a4cc"/></svg></h3><p>Lorem Ipsum has been the industry's standard dummy text ever since the 1500s, when an unknown printer took a galley of type and scrambled it to make a type specimen book. It has survived</p></div>

  <div class="card" style="left:99px;top:1561px"><h3>WHAT PAIN POINTS WILL THIS REMOVE FOR THEM?<svg width="11" height="11" viewBox="0 0 12 12"><circle cx="6" cy="6" r="6" fill="#fff"/><rect x="5.2" y="5" width="1.6" height="4.5" fill="#d2a4cc"/><circle cx="6" cy="3.3" r=".9" fill="#d2a4cc"/></svg></h3><p>Lorem Ipsum has been the industry's standard dummy text ever since the 1500s, when an unknown printer took a galley of type and scrambled it to make a type specimen book. It has survived</p></div>
  <div class="card" style="left:617px;top:1561px"><h3>HOW DO YOU SOLVE IT?<svg width="11" height="11" viewBox="0 0 12 12"><circle cx="6" cy="6" r="6" fill="#fff"/><rect x="5.2" y="5" width="1.6" height="4.5" fill="#d2a4cc"/><circle cx="6" cy="3.3" r=".9" fill="#d2a4cc"/></svg></h3><p>Lorem Ipsum has been the industry's standard dummy text ever since the 1500s, when an unknown printer took a galley of type and scrambled it to make a type specimen book. It has survived</p></div>

  <div class="card" style="left:99px;top:1758px"><h3>HOW ELSE COULD THIS PROBLEM BE SOLVED?<svg width="11" height="11" viewBox="0 0 12 12"><circle cx="6" cy="6" r="6" fill="#fff"/><rect x="5.2" y="5" width="1.6" height="4.5" fill="#d2a4cc"/><circle cx="6" cy="3.3" r=".9" fill="#d2a4cc"/></svg></h3><p>Lorem Ipsum has been the industry's standard dummy text ever since the 1500s, when an unknown printer took a galley of type and scrambled it to make a type specimen book. It has survived</p></div>
  <div class="card" style="left:617px;top:1758px"><h3>WHO OFFERS THESE OTHER SOLUTIONS?<svg width="11" height="11" viewBox="0 0 12 12"><circle cx="6" cy="6" r="6" fill="#fff"/><rect x="5.2" y="5" width="1.6" height="4.5" fill="#d2a4cc"/><circle cx="6" cy="3.3" r=".9" fill="#d2a4cc"/></svg></h3><p>Lorem Ipsum has been the industry's standard dummy text ever since the 1500s, when an unknown printer took a galley of type and scrambled it to make a type specimen book. It has survived</p></div>

  <div class="card" style="left:99px;top:1955px"><h3>WHY IS YOUR SOLUTION BETTER?<svg width="11" height="11" viewBox="0 0 12 12"><circle cx="6" cy="6" r="6" fill="#fff"/><rect x="5.2" y="5" width="1.6" height="4.5" fill="#d2a4cc"/><circle cx="6" cy="3.3" r=".9" fill="#d2a4cc"/></svg></h3><p>Lorem Ipsum has been the industry's standard dummy text ever since the 1500s, when an unknown printer took a galley of type and scrambled it to make a type specimen book. It has survived</p></div>
  <div class="card" style="left:617px;top:1955px"><h3>HOW MUCH DOES YOUR SOLUTION COST?<svg width="11" height="11" viewBox="0 0 12 12"><circle cx="6" cy="6" r="6" fill="#fff"/><rect x="5.2" y="5" width="1.6" height="4.5" fill="#d2a4cc"/><circle cx="6" cy="3.3" r=".9" fill="#d2a4cc"/></svg></h3><p>Lorem Ipsum has been the industry's standard dummy text ever since the 1500s, when an unknown printer took a galley of type and scrambled it to make a type specimen book. It has survived</p></div>

  <div class="card" style="left:99px;top:2152px"><h3>WHAT VALUE ARE YOU PROVIDING TO JUSTIFY THIS COST?<svg width="11" height="11" viewBox="0 0 12 12"><circle cx="6" cy="6" r="6" fill="#fff"/><rect x="5.2" y="5" width="1.6" height="4.5" fill="#d2a4cc"/><circle cx="6" cy="3.3" r=".9" fill="#d2a4cc"/></svg></h3><p>Lorem Ipsum has been the industry's standard dummy text ever since the 1500s, when an unknown printer took a galley of type and scrambled it to make a type specimen book. It has survived</p></div>
  <div class="card" style="left:617px;top:2152px"><h3>HOW WILL THIS MAKE THEIR LIFE/JOB EASIER/BETTER?<svg width="11" height="11" viewBox="0 0 12 12"><circle cx="6" cy="6" r="6" fill="#fff"/><rect x="5.2" y="5" width="1.6" height="4.5" fill="#d2a4cc"/><circle cx="6" cy="3.3" r=".9" fill="#d2a4cc"/></svg></h3><p>Lorem Ipsum has been the industry's standard dummy text ever since the 1500s, when an unknown printer took a galley of type and scrambled it to make a type specimen book. It has survived</p></div>

  <div class="save">SAVE CHANGES</div>
</section>

<footer class="footer">
  <small>© Copyright 2017 BloomPath. All Rights Reserved</small>
  <div class="social"><i></i><i></i><i></i><i></i></div>
</footer>

</body>
</html>
```